Coastline Premier Retreats Business Card Design

Design a business card for Coastline Premier Retreats. Look at the website for colors and reference. Card should have logo, name, title, office number, mobile number, email, URL and a tagline like, "Luxury Hotel & Resort Email Marketing" (This might change).

https://www.coastlinepremierretreats.example

The rest I will leave up to your imagination.

Contact Information for Business Card

Logo, name, title, office number, mobile number, email, URL and a tagline like, "Luxury Hotel & Resort Email Marketing" (This might change).

```html
<!DOCTYPE html>
<html lang="en">
<head>
<meta charset="utf-8">
<title>Coastline Premier Retreats – Business Card</title>
<link href="https://fonts.googleapis.com/css2?family=Arimo:wght@400;700&family=Montserrat:wght@400&display=swap" rel="stylesheet">
<style>
  :root {
    --stage: #2b2b2b;
    --card: #1b1b1b;
    --accent: #f07a12;
    --ink: #ffffff;
    --ink-soft: #e6e6e6;
  }
  * { box-sizing: border-box; margin: 0; padding: 0; }
  html, body {
    width: 1200px; height: 900px; overflow: hidden;
    background: var(--stage);
  }
  .stage {
    position: relative; width: 1200px; height: 900px;
    display: flex; flex-direction: column; align-items: center; justify-content: center; gap: 36px;
  }
  .card {
    position: relative; width: 680px; height: 388px;
    background: var(--card);
    border-bottom: 5px solid var(--accent);
    border-left: 3px solid var(--accent);
    box-shadow: 0 14px 30px rgba(0,0,0,.45);
    font-family: "Arimo", Arial, sans-serif;
    color: var(--ink);
  }
  /* Front */
  .card--front { display: flex; flex-direction: column; align-items: center; justify-content: center; }
  .brand-name {
    font-family: "Arimo", Arial, sans-serif; font-weight: 700;
    text-transform: uppercase; color: var(--ink);
    letter-spacing: 0.04em; line-height: 1.05; text-align: center;
  }
  .card--front .brand-name { font-size: 46px; }
  .tagline {
    margin-top: 70px;
    font-family: "Montserrat", Arial, sans-serif; font-size: 17px;
    color: var(--accent); letter-spacing: 0.06em;
  }
  /* Back */
  .card--back .brand-block {
    position: absolute; top: 44px; right: 44px;
    display: flex; align-items: center; gap: 12px;
  }
  .brand-square { width: 14px; height: 14px; background: var(--accent); }
  .card--back .brand-name { font-size: 22px; text-align: left; }
  .person { position: absolute; left: 60px; top: 200px; }
  .person-name {
    font-weight: 700; font-size: 32px; color: var(--accent);
    text-transform: uppercase; letter-spacing: 0.02em;
  }
  .person-title { font-size: 15px; color: var(--ink-soft); margin-top: 2px; }
  .rule {
    position: absolute; left: 60px; right: 44px; top: 276px;
    height: 1px; background: var(--accent);
  }
  .contacts {
    position: absolute; left: 60px; right: 44px; top: 298px;
    display: flex; font-size: 13.5px; color: var(--ink-soft);
  }
  .contact-group { padding: 0 18px; border-left: 1px solid var(--accent); }
  .contact-group:first-child { padding-left: 0; border-left: none; }
  .contact-line { display: flex; align-items: center; gap: 7px; line-height: 1.6; white-space: nowrap; }
  .contact-line svg { width: 12px; height: 12px; flex: none; }
</style>
</head>
<body>
<main class="stage">
  <section class="card card--front">
    <div class="brand-name">Coastline<br>Premier Retreats</div>
    <p class="tagline">Luxury Hotel &amp; Resort Email Marketing</p>
  </section>

  <section class="card card--back">
    <div class="brand-block">
      <span class="brand-square"></span>
      <span class="brand-name">Coastline<br>Premier Retreats</span>
    </div>

    <div class="person">
      <h1 class="person-name">Marcus Hale</h1>
      <p class="person-title">CEO/Founder</p>
    </div>

    <div class="rule"></div>

    <div class="contacts">
      <div class="contact-group">
        <p class="contact-line">
          <svg viewBox="0 0 12 12"><rect x="3" y="0.5" width="6" height="11" rx="1" fill="none" stroke="#f07a12"/><line x1="5" y1="9.5" x2="7" y2="9.5" stroke="#f07a12"/></svg>
          555.014.2270
        </p>
        <p class="contact-line">
          <svg viewBox="0 0 12 12"><path d="M1 4 Q6 0 11 4 L10 6 L8 5 L8 4 Q6 3 4 4 L4 5 L2 6 Z M2 7 H10 V11 H2 Z" fill="#f07a12"/></svg>
          +34 600 000 142
        </p>
      </div>
      <div class="contact-group">
        <p class="contact-line">
          <svg viewBox="0 0 12 12"><rect x="0.5" y="2" width="11" height="8" fill="#f07a12"/><path d="M0.5 2 L6 6.5 L11.5 2" fill="none" stroke="#1b1b1b"/></svg>
          info@coastlinepremierretreats.example
        </p>
        <p class="contact-line">
          <svg viewBox="0 0 12 12"><circle cx="6" cy="6" r="5.5" fill="#f07a12"/><path d="M0.5 6 H11.5 M6 0.5 Q3 6 6 11.5 M6 0.5 Q9 6 6 11.5" fill="none" stroke="#1b1b1b" stroke-width="0.8"/></svg>
          www.coastlinepremierretreats.example
        </p>
      </div>
      <div class="contact-group">
        <p class="contact-line">Po Box, 45 Harbor Rd</p>
        <p class="contact-line">Seaview, CA 90000</p>
      </div>
    </div>
  </section>
</main>
</body>
</html>
```